Veltrano.co - Polar Expeditions Specialists

We need a modern, visually striking business card for Veltrano.co, a company specialized in selling expedition cruises to the most remote regions on Earth, with a focus on the Arctic and Antarctica. The design should instantly communicate that the cardholder is an expert in polar travel. Use clean, premium aesthetics with cool tones like icy blue and white, possibly incorporating polar imagery (ice, glaciers, penguins, etc.)

Attached the logo

Contact Information for Business Card

Feels high-end and trustworthy.. Visually memorable — encourages people to keep it

Colors
0054AA
0677BA
7BADD7
CADEEF
E8F1F8

Requirements
Must have
• ice, glaciers, penguins, montains
Nice to have
• modern, transparente,

```html
<!DOCTYPE html>
<html lang="en">
<head>
<meta charset="utf-8">
<title>Veltrano.co – Business Card</title>
<link rel="stylesheet" href="https://fonts.googleapis.com/css2?family=Poppins:wght@300;400;500;600;700&display=swap">
<style>
  :root {
    --brand-blue: #2c78ba;
    --ink: #111111;
    --card-white: #ffffff;
    --backdrop: #e4e8ea;
  }
  * { box-sizing: border-box; margin: 0; padding: 0; }
  html, body {
    width: 1200px; height: 960px; overflow: hidden;
    background: var(--backdrop);
    font-family: "Poppins", sans-serif;
  }
  .card {
    position: absolute;
    left: 252px;
    width: 700px;
    height: 400px;
    background: var(--card-white);
    border-radius: 30px;
    border-left: 4px solid var(--brand-blue);
    border-bottom: 4px solid var(--brand-blue);
    overflow: hidden;
  }
  .card--front { top: 60px; }
  .card--back { top: 500px; }

  .brand-dot {
    position: absolute;
    border-radius: 50%;
    background: var(--brand-blue);
  }
  .brand-name {
    position: absolute;
    left: 0; right: 0;
    text-align: center;
    font-weight: 700;
    color: var(--brand-blue);
    line-height: 1;
    letter-spacing: -0.5px;
  }
  .brand-tagline {
    position: absolute;
    left: 0; right: 0;
    text-align: center;
    font-weight: 600;
    color: var(--brand-blue);
    line-height: 1;
  }

  /* front */
  .card--front .brand-dot { width: 120px; height: 120px; left: 286px; top: 62px; }
  .card--front .brand-name { top: 220px; font-size: 82px; }
  .card--front .brand-tagline { top: 307px; font-size: 23px; }

  /* back, left side */
  .back-brand { position: absolute; left: 0; top: 0; width: 345px; height: 400px; }
  .back-brand .brand-dot { width: 80px; height: 80px; left: 113px; top: 114px; }
  .back-brand .brand-name { top: 218px; font-size: 48px; }
  .back-brand .brand-tagline { top: 270px; font-size: 15px; }

  .divider {
    position: absolute;
    left: 345px; top: 73px;
    width: 2px; height: 254px;
    background: var(--brand-blue);
  }

  /* back, right side */
  .contact { position: absolute; left: 400px; top: 84px; color: var(--ink); }
  .contact-name {
    font-size: 37px; line-height: 1; color: var(--brand-blue);
    white-space: nowrap;
  }
  .contact-name .first { font-weight: 600; }
  .contact-name .last { font-weight: 300; }
  .contact-title { font-size: 18px; font-weight: 500; margin-top: 8px; line-height: 1.2; }
  .contact-address { font-size: 18px; font-weight: 400; margin-top: 14px; line-height: 1.45; }
  .contact-list { list-style: none; margin-top: 14px; }
  .contact-list li {
    display: flex; align-items: center; gap: 12px;
    font-size: 19px; line-height: 26px;
  }
  .contact-list svg { width: 17px; height: 17px; flex: none; fill: var(--brand-blue); }

  .footer-band {
    position: absolute; left: 0; right: 0; top: 354px;
    height: 26px; background: var(--brand-blue);
  }
  .footer-dot {
    position: absolute; left: 324px; top: 346px;
    width: 42px; height: 42px; border-radius: 50%;
    background: var(--brand-blue);
    border: 4px solid var(--card-white);
  }
</style>
</head>
<body>
  <section class="card card--front" aria-label="Card front">
    <div class="brand-dot"></div>
    <div class="brand-name">Veltrano.co</div>
    <div class="brand-tagline">Polar Expeditions Specialists</div>
  </section>

  <section class="card card--back" aria-label="Card back">
    <div class="back-brand">
      <div class="brand-dot"></div>
      <div class="brand-name">Veltrano.co</div>
      <div class="brand-tagline">Polar Expeditions Specialists</div>
    </div>

    <div class="divider"></div>

    <div class="contact">
      <div class="contact-name"><span class="first">Marta</span> <span class="last">Kovalen</span></div>
      <div class="contact-title">Founder &amp; CEO</div>
      <div class="contact-address">418 Lakeshore Ave. Suite 120<br>Denton, TX 76201</div>
      <ul class="contact-list">
        <li>
          <svg viewBox="0 0 24 24" aria-hidden="true"><path d="M6.6 10.8a15.1 15.1 0 0 0 6.6 6.6l2.2-2.2c.3-.3.7-.4 1-.2 1.1.4 2.3.6 3.6.6.6 0 1 .4 1 1V20c0 .6-.4 1-1 1C10.6 21 3 13.4 3 4c0-.6.4-1 1-1h3.5c.6 0 1 .4 1 1 0 1.3.2 2.5.6 3.6.1.3 0 .7-.2 1z"/></svg>
          (555) 214-3069
        </li>
        <li>
          <svg viewBox="0 0 24 24" aria-hidden="true"><path d="M12 2a10 10 0 1 0 0 20 10 10 0 0 0 0-20zm6.9 6h-3a15.6 15.6 0 0 0-1.4-3.6A8 8 0 0 1 18.9 8zM12 4c.8 1.2 1.5 2.5 1.9 4h-3.8c.4-1.5 1.1-2.8 1.9-4zM4.3 14a8.2 8.2 0 0 1 0-4h3.4a16.5 16.5 0 0 0 0 4zm.8 2h3a15.6 15.6 0 0 0 1.4 3.6A8 8 0 0 1 5.1 16zm3-8h-3a8 8 0 0 1 4.4-3.6C8.9 5.5 8.4 6.7 8.1 8zM12 20c-.8-1.2-1.5-2.5-1.9-4h3.8c-.4 1.5-1.1 2.8-1.9 4zm2.3-6H9.7a14.7 14.7 0 0 1 0-4h4.6a14.7 14.7 0 0 1 0 4zm.2 5.6c.6-1.1 1.1-2.3 1.4-3.6h3a8 8 0 0 1-4.4 3.6zm1.8-5.6a16.5 16.5 0 0 0 0-4h3.4a8.2 8.2 0 0 1 0 4z"/></svg>
          info@yourwebsite.com
        </li>
        <li>
          <svg viewBox="0 0 24 24" aria-hidden="true"><path d="M3 9l9-6 9 6v11a1 1 0 0 1-1 1H4a1 1 0 0 1-1-1zm2 1.6V19h14v-8.4l-7 4.7z"/></svg>
          www.yourwebsite.com
        </li>
      </ul>
    </div>

    <div class="footer-band"></div>
    <div class="footer-dot"></div>
  </section>
</body>
</html>
```